we can communicate on this, but i want to follow the approach we took on Pellew|Marsh & Quinlan but i feel the card front needs the black background and the platinum and gold logo. The back? I am open. we can use the same info from PM&Q. Velmont Arc is an enhanced equity investment fund - basically a very exclusive boutique hedge fund that uses only stock options. very advanced things. hope you are interested

Contact Information for Business Card

Dr. Lewis T. Brennick, CFA
Scientifique de fusée financière
701.555.0143
LTBquant47@mailvantor.com

4718 Willow Creek Bend W.
West Fargo, ND 58078

No web site

Colors

Designer to choose colors to be used in the design.

Requirements
Nice to have
• I tend to prefer the most visible applications of the logo to include logo and name, the logo version with a black background and the gold and platinum components separated by the black. I see this working well for a single side (logo and name - this is card front to me).
• I am fairly open to other treatments on the reverse side with the data. To me, it makes sense to have a different color rendition of the logo on the reverse and it may be a muted black tone on tone or an oversized portion that would have spot UV. Or, the reverse may play with colors and layout
Should not have
• Other colors = no no
• Decorative font

```html
<!DOCTYPE html>
<html lang="en">
<head>
<meta charset="utf-8">
<title>Velmont Arc — Business Card</title>
<link href="https://fonts.googleapis.com/css2?family=Montserrat:wght@600&family=Roboto:wght@400&family=Ubuntu:wght@500&display=swap" rel="stylesheet">
<style>
  :root {
    --backdrop: #3a3a3c;
    --card-black: #19191a;
    --card-black-deep: #111112;
    --watermark: #222224;
    --platinum: #e9e9eb;
    --gold: #d8ad2e;
    --gold-deep: #9a7217;
  }
  * { box-sizing: border-box; margin: 0; padding: 0; }
  html, body { width: 799px; height: 1200px; overflow: hidden; }
  body {
    background: var(--backdrop);
    font-family: "Roboto", sans-serif;
    position: relative;
  }
  .card {
    position: absolute;
    left: 80px;
    width: 640px;
    height: 366px;
    background: linear-gradient(160deg, var(--card-black) 0%, var(--card-black-deep) 100%);
    overflow: hidden;
  }
  .card--front { top: 140px; }
  .card--back { top: 700px; }

  /* Front: gold mark + platinum name on black */
  .front-mark {
    position: absolute;
    left: 346px; top: 52px;
    width: 120px; height: 120px;
    border-radius: 50%;
    background: linear-gradient(135deg, var(--gold) 0%, var(--gold-deep) 100%);
  }
  .front-name {
    position: absolute;
    left: 120px; top: 184px;
    font-family: "Montserrat", sans-serif;
    font-weight: 600;
    color: var(--platinum);
    line-height: 1;
  }
  .front-name__main { display: block; font-size: 62px; letter-spacing: 2px; }
  .front-name__sub { display: block; font-size: 24px; letter-spacing: 22px; margin-top: 12px; padding-left: 82px; }

  /* Back */
  .back-watermark {
    position: absolute;
    right: -110px; top: 110px;
    width: 340px; height: 340px;
    border-radius: 50%;
    background: var(--watermark);
  }
  .back-mark {
    position: absolute;
    left: 40px; top: 36px;
    width: 78px; height: 78px;
    border-radius: 50%;
    background: linear-gradient(135deg, var(--gold) 0%, var(--gold-deep) 100%);
  }
  .back-name {
    position: absolute;
    left: 138px; top: 44px;
    font-family: "Montserrat", sans-serif;
    font-weight: 600;
    color: var(--platinum);
    line-height: 1;
  }
  .back-name__main { display: block; font-size: 42px; letter-spacing: 1px; }
  .back-name__sub { display: block; font-size: 18px; letter-spacing: 20px; margin-top: 8px; }

  .person { position: absolute; left: 40px; top: 148px; }
  .person__name {
    font-family: "Ubuntu", sans-serif;
    font-weight: 500;
    font-size: 21px;
    color: var(--gold);
  }
  .person__title { font-size: 14px; color: var(--platinum); margin-top: 2px; }

  .divider {
    position: absolute;
    left: 40px; top: 200px;
    width: 560px; height: 2px;
    background: linear-gradient(90deg, var(--gold) 0%, var(--gold-deep) 70%, rgba(154,114,23,0.4) 100%);
  }

  .contact { position: absolute; left: 40px; top: 218px; list-style: none; }
  .contact__item {
    display: flex; align-items: center; gap: 10px;
    font-size: 15px; color: var(--platinum);
    margin-bottom: 8px;
  }
  .contact__icon { width: 14px; height: 14px; flex: none; }

  .address {
    position: absolute;
    right: 40px; bottom: 34px;
    text-align: right;
    font-style: normal;
    font-size: 16px;
    line-height: 1.45;
    color: var(--platinum);
  }
</style>
</head>
<body>
  <section class="card card--front" aria-label="Card front">
    <div class="front-mark"></div>
    <div class="front-name">
      <span class="front-name__main">VELMONT</span>
      <span class="front-name__sub">ARC</span>
    </div>
  </section>

  <section class="card card--back" aria-label="Card back">
    <div class="back-watermark"></div>
    <div class="back-mark"></div>
    <div class="back-name">
      <span class="back-name__main">VELMONT</span>
      <span class="back-name__sub">ARC</span>
    </div>

    <div class="person">
      <p class="person__name">Dr. Lewis T. Brennick, CFA</p>
      <p class="person__title">Scientifique de fusée financière</p>
    </div>

    <div class="divider"></div>

    <ul class="contact">
      <li class="contact__item">
        <svg class="contact__icon" viewBox="0 0 24 24" aria-hidden="true">
          <path fill="#d8ad2e" d="M6.6 10.8a15.1 15.1 0 0 0 6.6 6.6l2.2-2.2a1 1 0 0 1 1-.25 11.4 11.4 0 0 0 3.6.57 1 1 0 0 1 1 1V20a1 1 0 0 1-1 1A17 17 0 0 1 3 4a1 1 0 0 1 1-1h3.5a1 1 0 0 1 1 1c0 1.25.2 2.45.57 3.57a1 1 0 0 1-.25 1z"/>
        </svg>
        701.555.0143
      </li>
      <li class="contact__item">
        <svg class="contact__icon" viewBox="0 0 24 24" aria-hidden="true">
          <rect x="2" y="5" width="20" height="14" fill="#d8ad2e"/>
          <path d="M2 5l10 8 10-8" fill="none" stroke="#19191a" stroke-width="2"/>
        </svg>
        LTBquant47@mailvantor.com
      </li>
    </ul>

    <address class="address">
      4718 Willow Creek Bend W.<br>
      West Fargo, ND 58078
    </address>
  </section>
</body>
</html>
```